Carpet cleaning company focused on high quality needs business cards

We are a growing company that just merged with another company and need to design a new business card. We do both residential as well as commercial cleaning. We do carpet, tile & grout, upholstery, hard floors, and stain & pet odor removal. We treat our customers like family and strive to achieve outstanding results with every job.

```html
<!DOCTYPE html>
<html lang="en">
<head>
<meta charset="utf-8">
<title>Larkfield Floor Care – Business Card</title>
<link rel="stylesheet" href="https://fonts.googleapis.com/css2?family=Open+Sans:wght@400;700&family=Raleway:wght@700&display=swap">
<style>
  :root {
    --stage: #8f8f8f;
    --brand-red: #f04a43;
    --brand-red-deep: #dd3e38;
    --brand-red-faint: #e3433d;
    --card-white: #ffffff;
    --ink: #111111;
    --icon-red: #e8473f;
  }
  * { margin: 0; padding: 0; box-sizing: border-box; }
  html, body { width: 1200px; height: 1200px; overflow: hidden; }
  body { background: var(--stage); font-family: "Open Sans", Arial, sans-serif; position: relative; }

  .card { position: absolute; width: 798px; height: 465px; overflow: hidden; }

  /* Front */
  .card-front { left: 200px; top: 90px; background: var(--brand-red); }
  .front-wordmark {
    position: absolute; left: 0; right: 0; top: 150px;
    text-align: center;
    color: var(--brand-red-faint);
    font-family: "Open Sans", Arial, sans-serif;
    font-weight: 700; font-size: 64px; line-height: 1.12; letter-spacing: -1px;
  }

  /* Back */
  .card-back { left: 201px; top: 624px; width: 799px; background: var(--card-white); }
  .back-art { position: absolute; inset: 0; width: 799px; height: 465px; }

  .brand-lockup { position: absolute; left: 39px; top: 30px; display: flex; align-items: center; gap: 18px; }
  .brand-square { width: 76px; height: 76px; background: var(--brand-red); flex: none; }
  .brand-name {
    font-family: "Open Sans", Arial, sans-serif; font-weight: 700; color: var(--ink);
    font-size: 30px; line-height: 1.15;
  }

  .holder { position: absolute; left: 39px; top: 212px; }
  .holder-name { font-family: "Raleway", Arial, sans-serif; font-weight: 700; font-size: 35px; color: var(--ink); line-height: 1.1; }
  .holder-position { font-size: 16px; letter-spacing: 3.5px; color: var(--brand-red); margin-top: 2px; font-weight: 400; }

  .contact-list { position: absolute; left: 39px; top: 305px; list-style: none; }
  .contact-item { display: flex; align-items: center; height: 44px; font-size: 28px; color: var(--ink); }
  .contact-icon { width: 26px; height: 26px; margin-right: 19px; flex: none; }
</style>
</head>
<body>

<section class="card card-front" aria-label="Card front">
  <div class="front-wordmark">Larkfield<br>Floor Care</div>
</section>

<section class="card card-back" aria-label="Card back">
  <svg class="back-art" viewBox="0 0 799 465">
    <polygon points="505,0 799,0 799,465 649,465" fill="var(--brand-red)"/>
    <polygon role="img" aria-label="Faint mascot illustration of a smiling cleaner raising a steam cleaning wand"
             points="540,30 799,30 799,465 649,465 600,300" fill="var(--brand-red-deep)" opacity="0.45"/>
  </svg>

  <div class="brand-lockup">
    <div class="brand-square"></div>
    <div class="brand-name">Larkfield<br>Floor Care</div>
  </div>

  <div class="holder">
    <div class="holder-name">Name Surname</div>
    <div class="holder-position">POSITION</div>
  </div>

  <ul class="contact-list">
    <li class="contact-item">
      <svg class="contact-icon" viewBox="0 0 24 24"><path fill="var(--icon-red)" d="M6.6 10.8c1.4 2.8 3.8 5.1 6.6 6.6l2.2-2.2c.3-.3.7-.4 1-.2 1.1.4 2.3.6 3.6.6.6 0 1 .4 1 1V20c0 .6-.4 1-1 1C10.6 21 3 13.4 3 4c0-.6.4-1 1-1h3.5c.6 0 1 .4 1 1 0 1.3.2 2.5.6 3.6.1.3 0 .7-.2 1L6.6 10.8z"/></svg>
      (555) 014-2277
    </li>
    <li class="contact-item">
      <svg class="contact-icon" viewBox="0 0 24 24" fill="none" stroke="var(--icon-red)" stroke-width="1.8"><rect x="3" y="5" width="18" height="14" rx="1"/><path d="M3 6l9 7 9-7"/></svg>
      hello@larkfieldfloorcare.com
    </li>
    <li class="contact-item">
      <svg class="contact-icon" viewBox="0 0 24 24" fill="none" stroke="var(--icon-red)" stroke-width="1.5"><circle cx="12" cy="12" r="9"/><ellipse cx="12" cy="12" rx="4" ry="9"/><path d="M3 12h18M4.5 7.5h15M4.5 16.5h15"/></svg>
      larkfieldfloorcare.com
    </li>
  </ul>
</section>

</body>
</html>
```